UX - Need some screens design for a Skill Assessment Application

I am building an app to carry out skill assessments. Depending on how the assessment is configured, it may have one or more parts
1. Question based assessment (Multiple Choice, True False, Fill in the blanks"
2. Endorsement by two colleagues - A screen that allows user to pick colleagues based on search and shows the status of pending requests
3. A written submission - a page that explains the format of the submission and a file upload
As each assessment can be configured with or without any of the steps, the assessment UI must be such that these areas get hidden/displayed based on configuration.
Colour codes to be used can be #0e78bb and #ffffff
There will also be a start screen (instructions) and an end screen (results)
Target Market(s)
Enterprise software
Number of Pages Required
4 page

```html
<!DOCTYPE html>
<html lang="en">
<head>
<meta charset="utf-8">
<title>Endorsement</title>
<link href="https://fonts.googleapis.com/css2?family=Inter:wght@400;500;600;700&display=swap" rel="stylesheet">
<style>
:root{
  --brand:#0e78bb;
  --header:#0057a8;
  --white:#ffffff;
  --ink:#222831;
  --text:#4a4f57;
  --muted:#6b7079;
  --line:#dfe2e6;
  --head-bg:#f5f6f8;
  --pending-bg:#e6f2fb;
  --pending-ink:#0e5f99;
  --approved-bg:#dcf5ef;
  --approved-ink:#138a72;
  --disabled:#c3c7cc;
}
*{box-sizing:border-box;margin:0;padding:0}
html,body{width:1200px;height:686px;overflow:hidden;background:var(--white);font-family:"Inter",sans-serif;color:var(--ink)}
.topbar{height:43px;background:var(--header);display:flex;align-items:center;padding:0 56px 0 57px;color:var(--white)}
.brand{display:flex;align-items:center;gap:8px;font-size:15px;font-weight:500}
.brand-dot{width:20px;height:20px;border-radius:50%;background:var(--white)}
.nav{margin-left:auto;display:flex;align-items:center;gap:21px;font-size:12.5px}
.nav a{color:rgba(255,255,255,.8);text-decoration:none}
.nav a.active{color:var(--white);font-weight:600}
.user{display:flex;align-items:center;gap:4px;margin-left:0}
.user-photo{width:27px;height:27px;border-radius:50%;background:linear-gradient(135deg,#8a9bb5,#3d4a63)}
.page{padding:0 71px}
.crumb{margin-top:25px;font-size:11px;color:var(--text)}
.title-row{display:flex;justify-content:space-between;align-items:flex-start;margin-top:16px}
h1{font-size:22px;font-weight:600;line-height:1}
.subtitle{margin-top:14px;font-size:14px;color:var(--text)}
.btn-primary{margin-top:-2px;height:31px;width:164px;background:var(--brand);color:var(--white);border:0;border-radius:3px;font:500 12px "Inter",sans-serif;display:flex;align-items:center;justify-content:center;gap:7px}
.tabs{margin-top:14px;height:29px;border-bottom:1px solid var(--line);display:flex;align-items:flex-start;font-size:14px;position:relative}
.tab{color:var(--text);padding:0 17px;height:29px}
.tab.active{color:var(--brand);border-bottom:2px solid var(--brand);width:98px}
.tab.second{margin-left:42px}
.refresh{margin-left:auto;color:var(--brand);font-size:12.5px;font-weight:500;display:flex;align-items:center;gap:8px}
.table-card{margin-top:32px;border:1px solid var(--line);border-radius:4px;overflow:hidden}
table{width:100%;border-collapse:collapse;font-size:12px}
th{background:var(--head-bg);height:42px;text-align:left;font-weight:500;color:var(--text);padding-left:17px}
td{height:61px;border-top:1px solid var(--line);padding-left:17px;color:var(--text)}
td.category{color:var(--ink);font-weight:500}
.person{display:flex;align-items:center;gap:11px;color:var(--brand);font-weight:500}
.avatar{width:27px;height:27px;border-radius:50%}
.av1{background:linear-gradient(135deg,#c79a6a,#5a3a22)}
.av2{background:linear-gradient(135deg,#d8c9b8,#6e5a48)}
.av3{background:linear-gradient(135deg,#9cc8e6,#8a5a3e)}
.role{color:var(--text);font-size:12px}
.org{margin-top:3px;display:flex;align-items:center;gap:6px;color:var(--brand);font-size:10.5px}
.status-cell{display:flex;align-items:center;justify-content:space-between;padding-right:17px}
.pill{padding:5px 11px;border-radius:12px;font-size:11px;font-weight:500}
.pill.pending{background:var(--pending-bg);color:var(--pending-ink)}
.pill.approved{background:var(--approved-bg);color:var(--approved-ink)}
.btn-outline{width:112px;height:31px;border:1px solid var(--brand);border-radius:3px;background:var(--white);color:var(--brand);font:500 11.5px "Inter",sans-serif}
.kebab{width:112px;display:flex;justify-content:center}
.pager{border-top:1px solid var(--line);height:55px;display:flex;justify-content:center;align-items:center;gap:15px;font-size:11px}
.pg{height:31px;border:1px solid var(--line);border-radius:3px;color:var(--disabled);display:flex;align-items:center;justify-content:center;width:62px;gap:3px}
.pg.current{width:33px;background:var(--brand);border-color:var(--brand);color:var(--white);font-size:13px}
</style>
</head>
<body>
<header class="topbar">
  <div class="brand"><span class="brand-dot"></span><span>Skillgate</span></div>
  <nav class="nav">
    <a href="#">Assessments</a>
    <a href="#" class="active">Endorsement</a>
    <a href="#">Submissions</a>
    <a href="#">Results</a>
    <span class="user"><span class="user-photo" role="img" aria-label="User profile photo"></span>
      <svg width="10" height="10" viewBox="0 0 10 10"><path d="M2 3.5l3 3 3-3" fill="none" stroke="#fff" stroke-width="1.5"/></svg></span>
  </nav>
</header>
<main class="page">
  <p class="crumb">Assessment &nbsp;/</p>
  <div class="title-row">
    <div>
      <h1>Endorsement</h1>
      <p class="subtitle">Here are the complete details of assessments.</p>
    </div>
    <button class="btn-primary">
      <svg width="13" height="13" viewBox="0 0 14 14" fill="none" stroke="#fff" stroke-width="1.2"><rect x="1.5" y="7.5" width="11" height="5"/><path d="M7 1v5M5 3l2-2 2 2"/></svg>
      Request Endorsement
    </button>
  </div>
  <div class="tabs">
    <div class="tab active">All (3)</div>
    <div class="tab second">Pending (2)</div>
    <div class="refresh">
      <svg width="13" height="13" viewBox="0 0 14 14" fill="none" stroke="#0e78bb" stroke-width="1.6"><path d="M2.5 7a4.5 4.5 0 1 0 1.4-3.3"/><path d="M2.5 1.5v3h3"/></svg>
      Refresh
    </div>
  </div>
  <div class="table-card">
    <table>
      <colgroup><col style="width:239px"><col style="width:112px"><col style="width:122px"><col style="width:174px"><col style="width:196px"><col></colgroup>
      <thead><tr><th>Endorsements Category</th><th>Date Request</th><th>Effective Date</th><th>Endorsement</th><th>Skill &amp; Expertise</th><th>Status</th></tr></thead>
      <tbody>
        <tr>
          <td class="category">Application Design Capabilities</td><td>23/02/2024</td><td>29/02/2024</td>
          <td><div class="person"><span class="avatar av1" role="img" aria-label="Endorser photo"></span>Mei Lin Zhao</div></td>
          <td><div class="role">Senior Web Designer</div><div class="org"><svg width="12" height="10" viewBox="0 0 12 10" fill="none" stroke="#888" stroke-width="1"><rect x=".5" y="2.5" width="11" height="7"/><path d="M4 2.5V.5h4v2M.5 5.5h11"/></svg>Hao Ren Works Ltd.</div></td>
          <td><div class="status-cell"><span class="pill pending">Pending</span><button class="btn-outline">Cancel Request</button></div></td>
        </tr>
        <tr>
          <td class="category">UI/UX Designer</td><td>23/02/2024</td><td>29/02/2024</td>
          <td><div class="person"><span class="avatar av2" role="img" aria-label="Endorser photo"></span>Daniel Foster</div></td>
          <td><div class="role">UX Researcher</div><div class="org"><svg width="12" height="10" viewBox="0 0 12 10" fill="none" stroke="#888" stroke-width="1"><rect x=".5" y="2.5" width="11" height="7"/><path d="M4 2.5V.5h4v2M.5 5.5h11"/></svg>Brightbyte Corp.</div></td>
          <td><div class="status-cell"><span class="pill pending">Pending</span><button class="btn-outline">Cancel Request</button></div></td>
        </tr>
        <tr>
          <td class="category">Front-end Developer</td><td>12/01/2024</td><td>17/01/2024</td>
          <td><div class="person"><span class="avatar av3" role="img" aria-label="Endorser photo"></span>Owen Reyes Jr.</div></td>
          <td><div class="role">Lead Progammer</div><div class="org"><svg width="12" height="10" viewBox="0 0 12 10" fill="none" stroke="#888" stroke-width="1"><rect x=".5" y="2.5" width="11" height="7"/><path d="M4 2.5V.5h4v2M.5 5.5h11"/></svg>Brightbyte Corp.</div></td>
          <td><div class="status-cell"><span class="pill approved">Approved</span><span class="kebab"><svg width="4" height="16" viewBox="0 0 4 16" fill="#555"><circle cx="2" cy="2" r="1.6"/><circle cx="2" cy="8" r="1.6"/><circle cx="2" cy="14" r="1.6"/></svg></span></div></td>
        </tr>
      </tbody>
    </table>
    <div class="pager">
      <span class="pg"><svg width="6" height="8" viewBox="0 0 6 8"><path d="M5 1L2 4l3 3" fill="none" stroke="#c3c7cc" stroke-width="1.2"/></svg>Back</span>
      <span class="pg current">1</span>
      <span class="pg">Next<svg width="6" height="8" viewBox="0 0 6 8"><path d="M1 1l3 3-3 3" fill="none" stroke="#c3c7cc" stroke-width="1.2"/></svg></span>
    </div>
  </div>
</main>
</body>
</html>
```